Remodeling brochure

We need an informative homeowner friendly brochure detailing our company and things we do. We are looking for an initial setup and ideas (# of pages, etc) and then we will send more content. We are uploading our logo design. We are a high end remodeling company specializing in kitchen & bath remodels. We sell ourselves on customer communication and attention to detail in our designs and remodels.

Target Market(s)

Residential homeowners

Contact Information for Business Card

Modern and attention grabbing

Requirements
Must have
• Name- Hearth & Tile Works<br/>Address- 718 NW Larkfield Drive Suite #207<br/> Ankeny, Iowa 50099<br/>Phone- 515-555-0184<br/>email-htworksiowa@example-mail.com

```html
<!DOCTYPE html>
<html lang="en">
<head>
<meta charset="utf-8">
<title>Hearth &amp; Tile Works — Remodeling Brochure</title>
<link rel="stylesheet" href="https://fonts.googleapis.com/css2?family=Montserrat:wght@300;400;500;600;700;800&display=swap">
<style>
:root{
  --stage:#3b3b3b;
  --paper:#ffffff;
  --paper-shade:#f4f5f7;
  --ink:#2b2b2b;
  --ink-soft:#555a60;
  --blue:#1f86dc;
  --blue-deep:#1147c6;
  --sky:#3aa4ee;
  --teal:#0f6f73;
  --photo-warm-a:#d9c2a5;
  --photo-warm-b:#8d6a4c;
  --photo-cool-a:#e9ecef;
  --photo-cool-b:#9aa3a9;
}
*{box-sizing:border-box;margin:0;padding:0}
html,body{width:858px;height:1200px;overflow:hidden}
body{background:var(--stage);font-family:"Montserrat",sans-serif;color:var(--ink);position:relative}
.spread{position:absolute;left:29px;width:800px;height:560px;display:flex;box-shadow:0 10px 30px rgba(0,0,0,.45)}
.spread--covers{top:20px}
.spread--inside{top:620px}
.page{position:relative;width:400px;height:560px;background:var(--paper);overflow:hidden}
.page--left{background:linear-gradient(90deg,var(--paper) 88%,var(--paper-shade))}
.page--right{background:linear-gradient(90deg,var(--paper-shade),var(--paper) 12%)}
.abs{position:absolute}
.photo{position:absolute}
.photo--warm{background:linear-gradient(135deg,var(--photo-warm-a),var(--photo-warm-b))}
.photo--cool{background:linear-gradient(135deg,var(--photo-cool-a),var(--photo-cool-b))}
.photo--kitchen{background:linear-gradient(160deg,#f2f1ee 0%,#d8d4cc 45%,#8c8a84 100%)}
.wordmark{display:flex;align-items:center;gap:7px;font-weight:700;color:var(--blue-deep);letter-spacing:.3px}
.wordmark__square{background:var(--blue);display:block}
/* back cover */
.why{left:36px;top:300px;width:300px}
.heading{font-weight:700;font-size:14px;letter-spacing:.5px;color:var(--ink)}
.heading span{color:var(--blue)}
.body-copy{font-size:6.4px;line-height:1.55;color:var(--ink-soft)}
.ticks{list-style:none;margin-top:10px}
.ticks li{font-size:7px;font-weight:600;line-height:1.7;display:flex;align-items:center;gap:5px}
.ticks svg{width:7px;height:7px}
.contact{left:36px;top:410px;width:300px}
.contact__list{list-style:none;margin-top:8px;border-left:1px dashed var(--blue);margin-left:4px;padding-left:12px}
.contact__list li{font-size:7.5px;line-height:1.75;position:relative;color:var(--ink-soft)}
.contact__list li svg{position:absolute;left:-17px;top:3px;width:9px;height:9px}
/* front cover */
.cover-band{left:0;top:400px;width:400px;height:90px;background:linear-gradient(90deg,var(--blue),var(--blue-deep));clip-path:polygon(0 18%,100% 0,100% 82%,0 100%)}
.cover-band__lead{font-weight:800;font-size:17px;letter-spacing:2px;color:#fff}
.cover-band__sub{font-weight:300;font-size:11.5px;letter-spacing:.6px;color:#fff;margin-top:4px}
.url{font-size:7px;letter-spacing:2.5px;color:var(--ink-soft)}
/* inside */
.ribbon{position:absolute;height:30px;background:linear-gradient(90deg,var(--blue),var(--sky));color:#fff;font-weight:400;font-size:13px;letter-spacing:1.6px;display:flex;align-items:center;padding-left:18px}
.sub{font-weight:700;font-size:8.6px;color:var(--blue);margin-bottom:3px}
.block{position:absolute}
.brands-tab{font-size:6.5px;font-weight:600;color:#fff;background:var(--blue);padding:3px 10px;display:inline-block}
.brands{display:flex;gap:15px;margin-top:8px;font-size:7.5px;font-weight:700;color:var(--ink)}
.rule{position:absolute;height:1px;background:var(--blue)}
</style>
</head>
<body>

<section class="spread spread--covers">
  <!-- back cover -->
  <div class="page page--left">
    <div class="photo photo--warm" style="left:40px;top:55px;width:260px;height:150px" role="img" aria-label="Photo of a bright open dining room with wood panelling and white chairs"></div>
    <div class="abs" style="left:275px;top:40px;width:70px;height:135px;border:1px dashed var(--blue-deep)"></div>
    <div class="abs" style="left:270px;top:70px;width:44px;height:70px;background:var(--teal);opacity:.85"></div>
    <div class="photo photo--kitchen" style="left:330px;top:60px;width:70px;height:335px" role="img" aria-label="Kitchen interior photo continuing from the front cover"></div>
    <div class="abs" style="left:330px;top:395px;width:70px;height:95px;background:var(--blue);clip-path:polygon(0 0,100% 0,100% 90%,0 100%)"></div>

    <div class="abs why">
      <h2 class="heading">WHY <span>CHOOSE US</span></h2>
      <p class="body-copy" style="margin-top:6px">The number one reason why you should partner with us is that we are the only company in the state licensed to do warranty work. With us, you can be confident that your projects are in safe, dependable hands. Here are more reasons to choose us!</p>
      <ul class="ticks">
        <li><svg viewBox="0 0 10 10"><path d="M1 5l3 3 5-7" fill="none" stroke="#1f86dc" stroke-width="1.6"/></svg>Fully Insured and Licensed Business</li>
        <li><svg viewBox="0 0 10 10"><path d="M1 5l3 3 5-7" fill="none" stroke="#1f86dc" stroke-width="1.6"/></svg>Listed on HomePro Directory</li>
        <li><svg viewBox="0 0 10 10"><path d="M1 5l3 3 5-7" fill="none" stroke="#1f86dc" stroke-width="1.6"/></svg>Serves Residential and Commercial Clients</li>
        <li><svg viewBox="0 0 10 10"><path d="M1 5l3 3 5-7" fill="none" stroke="#1f86dc" stroke-width="1.6"/></svg>Various Payment Options Accepted</li>
      </ul>
    </div>

    <div class="abs contact">
      <h2 class="heading">CONTACT <span>INFO</span></h2>
      <ul class="contact__list">
        <li><svg viewBox="0 0 10 10"><path d="M5 1a3 3 0 0 1 3 3c0 2-3 5-3 5S2 6 2 4a3 3 0 0 1 3-3z" fill="#1f86dc"/></svg>718 NW Larkfield Drive Suite #207<br>Ankeny, Iowa 50099</li>
        <li><svg viewBox="0 0 10 10"><path d="M2 1h2l1 2-1 1a6 6 0 0 0 2 2l1-1 2 1v2c-4 1-8-3-7-7z" fill="#1f86dc"/></svg>515-555-0184</li>
        <li><svg viewBox="0 0 10 10"><rect x="1" y="2" width="8" height="6" fill="none" stroke="#1f86dc"/><path d="M1 2l4 3 4-3" fill="none" stroke="#1f86dc"/></svg>htworksiowa@example-mail.com</li>
        <li><svg viewBox="0 0 10 10"><circle cx="5" cy="5" r="3.5" fill="#1f86dc"/></svg>www.htworksiowa.com</li>
      </ul>
    </div>

    <div class="abs wordmark" style="left:250px;top:505px;font-size:8px">
      <span class="wordmark__square" style="width:14px;height:14px"></span>Hearth &amp; Tile Works
    </div>
  </div>

  <!-- front cover -->
  <div class="page page--right">
    <div class="abs wordmark" style="left:80px;top:28px;font-size:17px">
      <span class="wordmark__square" style="width:30px;height:30px"></span>Hearth &amp; Tile Works
    </div>
    <div class="photo photo--kitchen" style="left:0;top:80px;width:400px;height:330px" role="img" aria-label="Photo of a modern white kitchen with pendant lights, tall windows and a stone wall"></div>
    <div class="abs cover-band"></div>
    <div class="abs" style="left:0;top:420px;width:400px;text-align:right;padding-right:30px">
      <div class="cover-band__lead">WE SPECIALIZE IN</div>
      <div class="cover-band__sub">KITCHEN AND BATHROOM RENOVATIONS</div>
    </div>
    <div class="abs url" style="left:0;top:505px;width:400px;text-align:center">www.htworksiowa.com</div>
  </div>
</section>

<section class="spread spread--inside">
  <!-- inside left -->
  <div class="page page--left">
    <div class="ribbon" style="left:0;top:20px;width:400px">SUPERIOR REMODELING SERVICE</div>

    <div class="block" style="left:22px;top:70px;width:190px">
      <h3 class="sub">Kitchens, Bathrooms, &amp; Countertops</h3>
      <p class="body-copy">Get outstanding remodeling services from Hearth &amp; Tile Works in Ankeny, IA. We specialize in kitchen and bathroom remodel, counter installation as well as countertop sales. Our skilled craftsmen are knowledgeable in repairing and installing countertops made from various materials such as granite, quartz, marble, and soapstone.</p>
    </div>
    <div class="block" style="left:22px;top:160px;width:190px">
      <h3 class="sub">About Our Remodeling Company</h3>
      <p class="body-copy">Give your space a new breath of life! Get in touch with Hearth &amp; Tile Works and benefit from our comprehensive remodeling services. We also offer premium countertop sales and services. From redesigning your kitchens and bathrooms to installing, repairing, or laminating countertops, rest assured that we have your project needs covered. Call or email us should you require more information about our business.</p>
    </div>
    <div class="photo photo--warm" style="left:230px;top:62px;width:150px;height:150px" role="img" aria-label="Photos of a kitchen with wooden cabinets and a stone countertop"></div>

    <div class="ribbon" style="left:60px;top:268px;width:340px">UPGRADE YOUR COUNTERS</div>

    <div class="photo photo--cool" style="left:30px;top:320px;width:140px;height:170px" role="img" aria-label="Photos of a granite kitchen island and a marble bathroom vanity"></div>
    <div class="block" style="left:190px;top:318px;width:190px">
      <h3 class="sub">Countertop Installation and Repair</h3>
      <p class="body-copy">Do you want to enhance the function of your kitchen and bathroom? Perhaps you want to fix minor damage in your existing countertops? No matter what your needs are, Hearth &amp; Tile Works can help you. We are known for offering world-class countertop installation and repair services to residential and commercial properties in Ankeny, IA.</p>
    </div>
    <div class="block" style="left:190px;top:410px;width:190px">
      <h3 class="sub">Your Source for Quality Countertops</h3>
      <p class="body-copy">If you are in the market for the best countertop material for your space, look no further than Hearth &amp; Tile Works. Our services are not limited to countertop installation and maintenance. We also have a wide variety of countertop materials available for sale. Reach us today for more details about our product and service offerings.</p>
    </div>
  </div>

  <!-- inside right -->
  <div class="page page--right">
    <div class="ribbon" style="left:0;top:20px;width:400px">ENHANCE THE LOOK OF YOUR SPACE</div>

    <div class="block" style="left:22px;top:68px;width:215px">
      <h3 class="sub">Residential Kitchen and Bath Remodeling</h3>
      <p class="body-copy">Having a fulfilling mealtime with your family or a calming bath after a long day at work can easily drive your stress away. But does the current look of your kitchen and bathroom take away these simple joys from you? This is the time when having Hearth &amp; Tile Works in Ankeny, IA by your side comes to your advantage. We can create your own personal sanctuary at home by offering our residential kitchen and bath remodeling services.</p>
    </div>
    <div class="photo photo--warm" style="left:255px;top:62px;width:120px;height:95px" role="img" aria-label="Photo of a bathroom vanity with dark wood cabinets and round mirrors"></div>

    <div class="photo photo--cool" style="left:25px;top:175px;width:110px;height:100px" role="img" aria-label="Photo of a stainless steel commercial office kitchen"></div>
    <div class="block" style="left:150px;top:180px;width:230px">
      <h3 class="sub">Make Your Office Kitchen More Inviting</h3>
      <p class="body-copy">Do you find preparing meals a relaxing and gratifying task? Hire our remodelers today and allow us to do kitchen remodeling and redesigning not only for your home but also for your workplace. From building more room in your kitchen to installing suitable countertops in your office pantry, we have you covered. We carry different countertop materials for your added convenience.</p>
    </div>

    <div class="rule" style="left:150px;top:292px;width:230px"></div>
    <div class="block" style="left:25px;top:300px;width:360px">
      <span class="brands-tab">Brands We Carry Include</span>
      <div class="brands">
        <span>Quarzena</span><span>Veltrix</span><span>Corvane</span><span>Lamora</span><span>StoneHaven</span><span>Solvane</span>
      </div>
    </div>

    <svg class="abs" style="left:0;top:360px" width="400" height="200" viewBox="0 0 400 200" aria-hidden="true">
      <defs>
        <linearGradient id="cornerBlue" x1="0" y1="0" x2="1" y2="1">
          <stop offset="0" stop-color="#1f86dc"/>
          <stop offset="1" stop-color="#1147c6"/>
        </linearGradient>
      </defs>
      <polygon points="40,40 400,0 400,200 40,200" fill="url(#cornerBlue)"/>
      <g stroke="#ffffff" stroke-width="0.8" opacity=".75">
        <line x1="130" y1="80" x2="110" y2="110"/>
        <line x1="125" y1="130" x2="165" y2="145"/>
        <line x1="270" y1="60" x2="310" y2="75"/>
        <line x1="330" y1="100" x2="310" y2="125"/>
      </g>
    </svg>
  </div>
</section>

</body>
</html>
```